Dietitian needs awesome business card

I need a contemporary design that's eye catching but professional.
My card is to given to doctors, specialists and patients alike.
I manage patients with chronic diseases
I have uploaded my logo and current business card, I would also like the other Certified Clinical Nutritionist logo incorporated into the design

Target Market(s)

Doctors, specialists and patients

Industry/Entity Type

Healthcare

Contact Information for Business Card

www.brightfieldnutrition.com.au
Ph: 0427 561 903
Fax: 6457 2183
email: marcus.k.diet@fernmail.com
Space on the back of the card with: Appointment date, Appointment time and appointment location

Font styles to use
Serif

Colors
fbee3e
876aae
ffc214

Requirements
Must have
• My Logo
• Certified Clinical Nutritionist Logo
• My 4 locations - Pinebrook Medical Centre, North Corrin Health, Hollis Medical, Ashcombe Doctors Surgery
Nice to have
• I like the colours in my current business card

```html
<!DOCTYPE html>
<html lang="en">
<head>
<meta charset="utf-8">
<title>Brightfield Nutrition &amp; Dietetics – Business Card</title>
<link href="https://fonts.googleapis.com/css2?family=PT+Serif:ital,wght@0,400;0,700;1,400;1,700&display=swap" rel="stylesheet">
<style>
  :root {
    --stage: #161616;
    --card-white: #ffffff;
    --brand-blue: #1a4f9f;
    --brand-navy: #1d2a86;
    --brand-green: #9fd12a;
    --brand-green-deep: #6fb52c;
    --rule-lilac: #8f8ac4;
    --badge-orange: #f37021;
    --text-light: #ffffff;
  }
  * { box-sizing: border-box; margin: 0; padding: 0; }
  html, body { width: 1200px; height: 900px; overflow: hidden; }
  body {
    position: relative;
    background: var(--stage);
    font-family: "PT Serif", serif;
  }
  .card {
    position: absolute;
    top: 184px;
    height: 491px;
    border-radius: 12px;
    overflow: hidden;
    background: var(--card-white);
  }
  .card--front { left: 299px; width: 301px; background: var(--brand-blue); }
  .card--back { left: 645px; width: 304px; }

  .front-arc {
    position: absolute;
    left: -37.5px;
    top: -94px;
    width: 375px;
    height: 375px;
    border-radius: 50%;
    background: var(--card-white);
  }
  .brand-mark {
    position: absolute;
    border-radius: 50%;
    background: linear-gradient(135deg, var(--brand-navy) 0%, #1b83d0 45%, var(--brand-green) 70%, var(--brand-green-deep) 100%);
  }
  .card--front .brand-mark { left: 47px; top: 40px; width: 207px; height: 207px; }
  .card--back .brand-mark { left: 105px; top: 40px; width: 94px; height: 94px; }

  .front-details {
    position: absolute;
    left: 0; right: 0;
    top: 300px;
    text-align: center;
    color: var(--text-light);
  }
  .holder-name { color: var(--brand-green); font-weight: 700; font-size: 16px; margin-bottom: 16px; }
  .contact-line { font-size: 13px; line-height: 18px; }
  .credentials { margin-top: 18px; color: var(--brand-green); font-style: italic; font-weight: 700; font-size: 14px; line-height: 20px; }

  .practice-name {
    position: absolute;
    left: 0; right: 0;
    top: 160px;
    text-align: center;
    color: var(--brand-navy);
    font-weight: 700;
    font-size: 21px;
    line-height: 26px;
  }
  .locations {
    position: absolute;
    left: 0; right: 0;
    top: 222px;
    text-align: center;
    color: var(--brand-navy);
    font-size: 10.5px;
    line-height: 15px;
  }
  .appointment-lines { position: absolute; left: 63px; top: 274px; width: 178px; }
  .appointment-lines span { display: block; height: 1px; background: var(--rule-lilac); margin-bottom: 17.5px; }
  .notice {
    position: absolute;
    left: 0; right: 0;
    top: 326px;
    text-align: center;
    color: var(--brand-navy);
    font-size: 13px;
    line-height: 18px;
  }
  .member-badge { position: absolute; left: 122px; top: 391px; }
</style>
</head>
<body>
  <section class="card card--front">
    <div class="front-arc"></div>
    <div class="brand-mark" role="img" aria-label="Practice logo symbol area"></div>
    <div class="front-details">
      <p class="holder-name">Marcus Kellaway</p>
      <p class="contact-line">0427 561 903</p>
      <p class="contact-line">6457 2183</p>
      <p class="contact-line">marcus.k.diet@fernmail.com</p>
      <p class="contact-line">www.brightfieldnutrition.com.au</p>
      <p class="credentials">Certified Clinical Nutritionist<br>Nutritionist and Chef</p>
    </div>
  </section>

  <section class="card card--back">
    <div class="brand-mark" role="img" aria-label="Practice logo symbol area"></div>
    <p class="practice-name">Brightfield<br>Nutrition &amp; Dietetics</p>
    <p class="locations">Pinebrook Medical Centre · North Corrin Health<br>Hollis Medical · Ashcombe Doctors Surgery</p>
    <div class="appointment-lines"><span></span><span></span><span></span></div>
    <p class="notice">If unable to keep appointment,<br>kindly give 24hrs notice.</p>
    <svg class="member-badge" width="62" height="67" viewBox="0 0 62 67" role="img" aria-label="Professional membership badge">
      <rect x="0" y="0" width="62" height="67" rx="3" fill="var(--badge-orange)"/>
    </svg>
  </section>
</body>
</html>
```